Design bcard for Valtrove Consulting and Training LLC

I need a logo inspired by the term Valtrove. I'd like to have type of work I do on the back side, i.e. provide V and T on DEIJ, SDOH,...... Front of card--business name, contact information, and possibly a tag line.

Target Market(s)

NGOs, human service agencies, education, healthcare, public health.

Contact Information for Business Card

Name of business, email address, phone number, logo--on front. Services on the back

Font styles to use
Sans Serif

Requirements
Must have
• Contact information, creative logo, services

```html
<!DOCTYPE html>
<html lang="en">
<head>
<meta charset="utf-8">
<title>Valtrove Consulting and Training LLC – Business Card</title>
<link rel="stylesheet" href="https://fonts.googleapis.com/css2?family=Lato:wght@400;700;900&display=swap">
<style>
  :root {
    --bg: #3b3b3d;
    --green: #2f6b35;
    --green-light: #a8d3ab;
    --white: #ffffff;
    --ink: #2f6b35;
    --ink-soft: #3d3d3d;
  }
  * { box-sizing: border-box; margin: 0; padding: 0; }
  html, body { width: 1200px; height: 689px; overflow: hidden; background: var(--bg); }
  body { font-family: "Lato", sans-serif; position: relative; }

  .card {
    position: absolute;
    top: 190px;
    width: 550px;
    height: 314px;
    border-radius: 18px;
    overflow: hidden;
    box-shadow: 0 18px 40px rgba(0,0,0,.45);
  }

  /* Back side: services */
  .card--back { left: 35px; background: var(--green); color: var(--white); }
  .card--back .brand { position: absolute; left: 0; right: 0; top: 78px; text-align: center; }
  .brand-name {
    display: inline-flex; align-items: center; gap: 12px;
    font-weight: 900; font-size: 64px; letter-spacing: 1px; line-height: 1;
  }
  .brand-dot { width: 18px; height: 18px; border-radius: 50%; background: currentColor; }
  .brand-sub {
    display: block; margin-top: 8px;
    font-weight: 400; font-size: 15px; letter-spacing: 4.5px;
  }
  .services {
    position: absolute; left: 20px; right: 20px; bottom: 44px;
    text-align: center; font-size: 13px; line-height: 1.55;
  }

  /* Front side: contact */
  .card--front { left: 615px; background: var(--white); }
  .card--front .brand { position: absolute; left: 28px; top: 58px; color: var(--ink); }
  .card--front .brand-name { font-size: 40px; gap: 9px; }
  .card--front .brand-dot { width: 12px; height: 12px; }
  .card--front .brand-sub { font-size: 9.5px; letter-spacing: 2.6px; margin-top: 6px; }

  .person { position: absolute; right: 36px; top: 46px; text-align: right; color: var(--ink); }
  .person-name { font-weight: 900; font-size: 21px; letter-spacing: 1px; line-height: 1.1; }
  .person-title { font-size: 13px; color: var(--ink-soft); margin-top: 3px; }

  .contact { position: absolute; left: 44px; top: 140px; list-style: none; color: var(--ink-soft); font-size: 12.5px; }
  .contact li { display: flex; align-items: center; gap: 9px; height: 17px; }
  .contact svg { width: 11px; height: 11px; fill: var(--ink); flex: none; }

  .wave { position: absolute; left: 0; bottom: 0; width: 550px; height: 314px; }
  .tagline {
    position: absolute; right: 34px; bottom: 22px;
    color: var(--white); font-size: 13px; letter-spacing: 1px; font-weight: 400;
  }
</style>
</head>
<body>

<section class="card card--back" aria-label="Back of card">
  <div class="brand">
    <span class="brand-name"><span class="brand-dot"></span>VALTROVE</span>
    <span class="brand-sub">CONSULTING AND TRAINING LLC</span>
  </div>
  <p class="services">
    Health Care &amp; Quality | Neighborhood &amp; Built Environment | Economic Stability<br>
    Social and Community Context | Education Access and Quality
  </p>
</section>

<section class="card card--front" aria-label="Front of card">
  <svg class="wave" viewBox="0 0 550 314" aria-hidden="true">
    <path d="M0 254 C180 252 400 205 550 118 L550 128 C400 216 180 262 0 264 Z" fill="var(--green-light)"/>
    <path d="M0 270 C180 268 400 222 550 134 L550 314 L0 314 Z" fill="var(--green)"/>
  </svg>

  <div class="brand">
    <span class="brand-name"><span class="brand-dot"></span>VALTROVE</span>
    <span class="brand-sub">CONSULTING AND TRAINING LLC</span>
  </div>

  <div class="person">
    <div class="person-name">DANA WHITFIELD</div>
    <div class="person-title">Founder &amp; CEO</div>
  </div>

  <ul class="contact">
    <li><svg viewBox="0 0 24 24"><path d="M6.6 10.8a15 15 0 0 0 6.6 6.6l2.2-2.2c.3-.3.7-.4 1-.2 1.1.4 2.3.6 3.6.6.6 0 1 .4 1 1V20c0 .6-.4 1-1 1C10.6 21 3 13.4 3 4c0-.6.4-1 1-1h3.5c.6 0 1 .4 1 1 0 1.3.2 2.5.6 3.6.1.3 0 .7-.2 1z"/></svg>(555) 201-7430</li>
    <li><svg viewBox="0 0 24 24"><path d="M7 1h10a2 2 0 0 1 2 2v18a2 2 0 0 1-2 2H7a2 2 0 0 1-2-2V3a2 2 0 0 1 2-2zm0 3v14h10V4zm5 15.5a1.2 1.2 0 1 0 0 2.4 1.2 1.2 0 0 0 0-2.4z"/></svg>(555) 318-9052</li>
    <li><svg viewBox="0 0 24 24"><path d="M6 2h12v5H6zM4 8h16a2 2 0 0 1 2 2v7h-4v5H6v-5H2v-7a2 2 0 0 1 2-2zm4 8v4h8v-4z"/></svg>(555) 462-1187</li>
    <li><svg viewBox="0 0 24 24"><path d="M2 5h20v14H2zm2 2v.5l8 5 8-5V7z"/></svg>hello@valtrove.example</li>
    <li><svg viewBox="0 0 24 24"><path d="M12 2a10 10 0 1 0 0 20 10 10 0 0 0 0-20zm0 2c1 0 2.3 2.1 2.8 5H9.2C9.7 6.1 11 4 12 4zM4.3 11h3.8c0 .7 0 1.4.1 2H4.3a8 8 0 0 1 0-2zm4.9 4h5.6c-.5 2.9-1.8 5-2.8 5s-2.3-2.1-2.8-5zm6.7-4h3.8a8 8 0 0 1 0 2h-3.8c.1-.6.1-1.3 0-2z"/></svg>valtrove.example</li>
  </ul>

  <p class="tagline">YOUR TAGLINE GOES HERE</p>
</section>

</body>
</html>
```